Marava Cove Lodge Christmas wishes 2013

We require postcards designed to mail our to our clients for Christmas. We are a SURF travel company, with a high end market and like to mail our Christmas postcards to all our guests that have stayed with us through the year. Front cover will have images and text (ie Seasons Greeting) and our logo. The back will have space for TO: name & address and postage stamp. Will also have some basic text (ie The Management & Staff at Marava Cove Lodge wish you and your family all the best for the Festive Season and New Year. We look forward to seeing you back at Marava Cove Lodge again soon etc etc). Here is link to main image https://www.filecrate-example.com/sh/qwmxrtz481plo/Vb7kRtPwqN

Target Market(s)

Our clients are mostly mature men (40-70) surfers who purchase luxury surf trips

Industry/Entity Type

Travel

Requirements
Must have
• Ocean Image (front)
Logo x 2 in same colour - Orindel & Marava Cove Lodge (front)
Text (front)
Back to be white
Space for name & address (back)
Space for postage stamp (back)
Message (back)
Website www.orindellodges-example.com (back)

```html
<!DOCTYPE html>
<html lang="en">
<head>
<meta charset="utf-8">
<title>Marava Cove Lodge – Season's Greetings Postcard</title>
<link href="https://fonts.googleapis.com/css2?family=Arimo:wght@400;700&family=Varela+Round&display=swap" rel="stylesheet">
<style>
  :root {
    --stage: #ececec;
    --card-white: #ffffff;
    --ink: #2a2a2a;
    --on-photo: #ffffff;
    --stamp-line: #a9a9a9;
    --sea-light: #2fa58f;
    --sea-mid: #1b6f86;
    --sea-deep: #0b2a57;
    --sky: #1f4fc4;
  }
  * { margin: 0; padding: 0; box-sizing: border-box; }
  html, body { width: 1200px; height: 1000px; overflow: hidden; }
  body { position: relative; background: var(--stage); font-family: "Arimo", Arial, sans-serif; }

  .postcard { position: absolute; width: 563px; height: 375px; overflow: hidden; }
  .postcard--front { left: 324px; top: 58px; }
  .postcard--back { left: 325px; top: 509px; background: var(--card-white); }

  .front-photo {
    position: absolute; inset: 0;
    background:
      linear-gradient(90deg, transparent 55%, rgba(31,79,196,0.9) 75%, var(--sky) 100%),
      linear-gradient(180deg, var(--sea-light) 0%, var(--sea-mid) 45%, var(--sea-deep) 100%);
  }
  .front-headline {
    position: absolute; left: 56px; top: 45px;
    color: var(--on-photo); font-weight: 700; font-size: 22px; letter-spacing: -0.3px;
  }
  .brand-lodge {
    position: absolute; left: 112px; top: 318px; width: 120px;
    display: flex; flex-direction: column; align-items: center; gap: 6px;
    color: var(--on-photo); font-family: "Varela Round", Arial, sans-serif;
  }
  .brand-lodge__mark { width: 22px; height: 22px; border: 2px solid var(--on-photo); border-radius: 50%; }
  .brand-lodge__name { font-size: 11px; white-space: nowrap; }
  .brand-lodge__place { font-size: 8px; letter-spacing: 1px; margin-top: -4px; }
  .brand-group {
    position: absolute; left: 287px; top: 328px;
    display: flex; align-items: center; gap: 10px;
    color: var(--on-photo); font-family: "Varela Round", Arial, sans-serif;
    font-size: 10px; letter-spacing: 1.6px;
  }
  .brand-group__mark { width: 14px; height: 14px; border: 2px solid var(--on-photo); border-radius: 50%; }

  .back-message {
    position: absolute; left: 37px; top: 96px; width: 170px;
    font-family: "Varela Round", Arial, sans-serif; font-size: 10.5px; line-height: 14.5px;
    color: var(--ink); text-align: justify; font-weight: 700;
  }
  .back-message p + p { margin-top: 14px; }
  .back-website {
    position: absolute; left: 51px; top: 261px;
    font-size: 10px; font-weight: 700; color: var(--ink); letter-spacing: -0.3px;
  }
  .address-field {
    position: absolute; left: 243px;
    font-family: "Varela Round", Arial, sans-serif; font-size: 12px; color: var(--ink);
  }
  .address-field--name { top: 95px; }
  .address-field--address { top: 127px; }
  .stamp-box {
    position: absolute; left: 452px; top: 38px; width: 69px; height: 69px;
    border: 3px solid var(--stamp-line);
  }
</style>
</head>
<body>
  <section class="postcard postcard--front">
    <div class="front-photo" role="img" aria-label="Ocean photograph: surfer riding inside a breaking turquoise wave under a blue sky, mountains on the horizon"></div>
    <h1 class="front-headline">Seasons Greetings!</h1>
    <div class="brand-lodge">
      <span class="brand-lodge__mark"></span>
      <span class="brand-lodge__name">maravacovelodge-example.com</span>
      <span class="brand-lodge__place">indonesia</span>
    </div>
    <div class="brand-group">
      <span class="brand-group__mark"></span>
      <span class="brand-group__name">ORINDEL LODGES &amp; RESORTS</span>
    </div>
  </section>

  <section class="postcard postcard--back">
    <div class="back-message">
      <p>The Management &amp; Staff at Marava Cove Lodge wish you and your family all the best for the Festive Season and New Year.</p>
      <p>We look forward to seeing you back at Marava Cove Lodge again soon!</p>
    </div>
    <div class="back-website">WWW.ORINDELLODGES-EXAMPLE.COM</div>
    <div class="address-field address-field--name">name</div>
    <div class="address-field address-field--address">address</div>
    <div class="stamp-box"></div>
  </section>
</body>
</html>
```